Labour Day banner showcasing 20% off site

Banner graphic promoting our Labour Day sale
Size: 2000px x 600px
- examples from other companies and their sale banners have been uploaded for inspiration. Labour day examples are for the United States's holiday and submissions should NOT be in their country colours.
- product images can be found at www.flormaplex.com

Target Market(s)

19+

Industry/Entity Type

Cannabis

Requirements
Must have
• Phrases:
- “Happy Labour Day”
- “20% off site wide sale*"
- "Coupon code: Kestrel20"
- Underneath phrase the date of sale “September 3rd - 7th”
- In tiny print “*excludes all sale and bundled items”
- MUST BE 2000px x 600px
Nice to have
• - images of the products or bud we carry which can be found at www.flormaplex.com
- bold
Should not have
• - company logo
- the American flag, we are a Canadian company, colours and flag should all be Canadian

```html
<!DOCTYPE html>
<html lang="en">
<head>
<meta charset="utf-8">
<title>Labour Day Sale Banner</title>
<link href="https://fonts.googleapis.com/css2?family=Bowlby+One&family=Montserrat:wght@400;700;800&family=Yellowtail&display=swap" rel="stylesheet">
<style>
  :root {
    --maple-red: #e1191f;
    --maple-red-light: #ea3a3f;
    --navy: #22295e;
    --paper: #ffffff;
  }
  html, body {
    margin: 0;
    padding: 0;
    overflow: hidden;
    background: var(--paper);
  }
  .banner {
    position: relative;
    width: 1200px;
    height: 360px;
    overflow: hidden;
    background: var(--paper);
    font-family: "Montserrat", sans-serif;
  }
  .backdrop {
    position: absolute;
    inset: 0;
  }
  .brand {
    position: absolute;
    left: 24px;
    top: 40px;
    display: flex;
    align-items: center;
    gap: 8px;
    color: var(--paper);
    font-weight: 800;
    font-size: 22px;
    letter-spacing: 0.2px;
  }
  .brand-mark {
    width: 14px;
    height: 14px;
    background: var(--paper);
  }
  .greeting {
    position: absolute;
    left: 230px;
    top: 40px;
    width: 320px;
    height: 280px;
  }
  .greeting text {
    font-family: "Yellowtail", cursive;
    fill: var(--navy);
    stroke: var(--paper);
    stroke-width: 6px;
    stroke-linejoin: round;
    paint-order: stroke;
  }
  .headline {
    position: absolute;
    left: 876px;
    top: 26px;
    width: 300px;
    height: 210px;
  }
  .headline text {
    fill: var(--paper);
    font-family: "Bowlby One", sans-serif;
  }
  .sale-dates {
    position: absolute;
    left: 882px;
    top: 244px;
    width: 290px;
    text-align: center;
    color: var(--paper);
    font-weight: 700;
    font-size: 18.5px;
    white-space: nowrap;
  }
  .sale-dates sup {
    font-size: 10px;
    vertical-align: 8px;
    line-height: 0;
  }
  .coupon {
    position: absolute;
    left: 883px;
    top: 279px;
    width: 285px;
    height: 41px;
    background: var(--paper);
    color: var(--maple-red);
    display: flex;
    align-items: center;
    justify-content: center;
    font-size: 19px;
    font-weight: 400;
    white-space: nowrap;
  }
  .coupon-code {
    font-weight: 800;
    margin-left: 4px;
  }
  .fine-print {
    position: absolute;
    right: 32px;
    top: 326px;
    color: var(--paper);
    font-weight: 700;
    font-size: 9px;
    white-space: nowrap;
  }
</style>
</head>
<body>
<div class="banner">
  <svg class="backdrop" width="1200" height="360" viewBox="0 0 1200 360">
    <defs>
      <radialGradient id="leafGlow" cx="0.5" cy="0.5" r="0.5">
        <stop offset="0" stop-color="#e1191f"/>
        <stop offset="0.75" stop-color="#e1191f"/>
        <stop offset="1" stop-color="#e1191f" stop-opacity="0"/>
      </radialGradient>
      <linearGradient id="rightLeaves" x1="0" y1="0" x2="0" y2="1">
        <stop offset="0" stop-color="#e1191f"/>
        <stop offset="1" stop-color="#f06a6d"/>
      </linearGradient>
    </defs>
    <polygon class="corner-band" points="0,0 294,0 0,274" fill="var(--maple-red)"/>
    <polygon class="side-band" points="822,0 1200,0 1200,360 546,360" fill="var(--maple-red)"/>
    <polygon role="img" aria-label="White cannabis leaf silhouettes scattered across the red band"
             points="822,0 876,0 876,360 546,360" fill="url(#rightLeaves)"/>
    <ellipse role="img" aria-label="Large red maple-cannabis leaf behind the greeting"
             cx="405" cy="180" rx="205" ry="172" fill="url(#leafGlow)"/>
  </svg>

  <div class="brand">
    <span class="brand-mark"></span>
    <span class="brand-name">Flormaplex</span>
  </div>

  <svg class="greeting" viewBox="0 0 320 280" width="320" height="280">
    <g transform="rotate(-8 160 140)">
      <text x="112" y="72" font-size="62">Happy</text>
      <text x="20" y="160" font-size="104">Labour</text>
      <text x="108" y="258" font-size="112">Day</text>
    </g>
  </svg>

  <svg class="headline" viewBox="0 0 300 210" width="300" height="210">
    <text x="2" y="58" font-size="74" textLength="294" lengthAdjust="spacingAndGlyphs">20% OFF</text>
    <text x="8" y="112" font-size="54" textLength="286" lengthAdjust="spacingAndGlyphs">SITE WIDE</text>
    <text x="6" y="206" font-size="112" textLength="290" lengthAdjust="spacingAndGlyphs">SALE</text>
  </svg>

  <div class="sale-dates">September 3<sup>rd</sup> &nbsp;- &nbsp;7<sup>th</sup>, 2020</div>

  <div class="coupon">Coupon Code : <span class="coupon-code">Kestrel20</span></div>

  <div class="fine-print">*excludes all sale and bundled items</div>
</div>
</body>
</html>
```